Dental specialist needs a sharp looking letterhead

I am looking for a letterhead to be used to send letters and communication between myself (a dental specialist) and other dentists.
My office is a state of the art dental specialty office.
I need to letterhead to also state:
Bertram L. Oswick DDS
2748 Tollard Avenue, Suite K
West Tollard, NY 14391
(716)392-5061
fax: (716)392-5087
oswickroot.com (**this email address may change)

i included my logo designs.
thank you

Target Market(s)

dentists

Industry/Entity Type

Communication

Requirements
Must have
• the included logo, whether the vertical or horizontal versions

```html
<!DOCTYPE html>
<html lang="en">
<head>
<meta charset="utf-8">
<title>Quillbrae Endodontics P.C. — Letterhead</title>
<link rel="stylesheet" href="https://fonts.googleapis.com/css2?family=Open+Sans:wght@400;600;700&display=swap">
<style>
  :root {
    --backdrop: #8f8f8f;
    --paper: #ffffff;
    --ink: #2b2b2b;
    --brand-blue: #29b6f6;
    --brand-green: #7cc242;
    --logo-ink: #1f1f1f;
  }
  * { box-sizing: border-box; margin: 0; padding: 0; }
  html, body { width: 1200px; height: 916px; overflow: hidden; }
  body {
    background: var(--backdrop);
    font-family: "Open Sans", Arial, sans-serif;
    color: var(--ink);
    position: relative;
  }
  .letterhead {
    position: absolute;
    left: 260px; top: 18px;
    width: 680px; height: 880px;
    background: var(--paper);
    box-shadow: 0 6px 24px rgba(0,0,0,.25);
    overflow: hidden;
  }
  .sender {
    position: absolute;
    top: 34px; right: 40px;
    text-align: right;
    letter-spacing: 2px;
  }
  .sender__name { color: var(--brand-blue); font-size: 13px; font-weight: 600; }
  .sender__title { color: var(--brand-green); font-size: 10px; font-weight: 600; margin-top: 2px; }
  .sender__tab {
    position: absolute;
    top: 30px; right: 0;
    width: 12px; height: 34px;
    background: var(--brand-blue);
  }
  .brand {
    position: absolute;
    top: 98px; left: 52px;
    display: flex; align-items: center; gap: 10px;
  }
  .brand__mark { width: 22px; height: 22px; border-radius: 50%; background: var(--brand-blue); flex: none; }
  .brand__name {
    color: var(--logo-ink);
    font-size: 16px; font-weight: 700;
    letter-spacing: .5px;
    white-space: nowrap;
  }
  .letter {
    position: absolute;
    top: 210px; left: 80px; right: 80px;
    font-size: 10.5px; line-height: 1.55;
  }
  .letter p { margin-bottom: 12px; }
  .letter__greeting { margin-bottom: 12px; }
  .letter__closing { position: absolute; top: 560px; left: 80px; font-size: 10.5px; }
  .footer-rule {
    position: absolute;
    left: 0; right: 0; bottom: 114px;
    height: 3px; background: var(--brand-green);
  }
  .footer-band {
    position: absolute;
    left: 0; right: 0; bottom: 78px;
    height: 32px;
    background: var(--brand-blue);
    color: #fff;
    font-size: 11.5px;
    display: flex; align-items: center; justify-content: center;
    letter-spacing: .3px;
    white-space: nowrap;
  }
  .footer-band span + span::before { content: "|"; margin: 0 8px; }
  .footer-web {
    position: absolute;
    left: 0; right: 0; bottom: 52px;
    text-align: center;
    font-size: 11px; font-weight: 600;
    letter-spacing: 5px;
    color: var(--ink);
  }
</style>
</head>
<body>
  <main class="letterhead">
    <div class="sender">
      <div class="sender__name">Bertram L. Oswick</div>
      <div class="sender__title">D.D.S</div>
    </div>
    <div class="sender__tab"></div>

    <div class="brand">
      <span class="brand__mark"></span>
      <span class="brand__name">Quillbrae Endodontics P.C.</span>
    </div>

    <section class="letter">
      <div class="letter__greeting">Lorem ipsum,</div>
      <p>Lorem ipsum dolor sit amet, consectetuer adipiscing elit. Nam cursus. Morbi ut mi. Nullam enim leo, egestas id, condimentum at, laoreet mattis, massa. Sed eleifend nonummy diam. Praesent mauris ante, elementum et, bibendum at, posuere sit amet, nibh. Duis tincidunt lectus quis dui viverra vestibulum. Suspendisse vulputate aliquam dui. Nulla elementum dui ut augue.</p>
      <p>Aliquam vehicula mi at mauris. Maecenas placerat, nisl at consequat rhoncus, sem nunc gravida justo, quis eleifend arcu velit quis lacus. Morbi magna magna, tincidunt a, mattis non, imperdiet vitae, tellus.</p>
      <p>Mauris nunc quam, venenatis nec, euismod sit amet, egestas placerat, est. Pellentesque habitant morbi tristique senectus et netus et malesuada fames ac turpis egestas. Cras id elit. Integer quis urna.</p>
      <p>Aliquam vehicula mi at mauris. Maecenas placerat, nisl at consequat rhoncus, sem nunc gravida justo, quis eleifend arcu velit quis lacus. Morbi magna magna, tincidunt a, mattis non, imperdiet vitae, tellus.</p>
      <p>Mauris nunc quam, venenatis nec, euismod sit amet, egestas placerat, est. Pellentesque habitant morbi tristique senectus et netus et malesuada fames ac turpis egestas. Cras id elit. Integer quis urna.</p>
    </section>
    <div class="letter__closing">Sincerly,</div>

    <div class="footer-rule"></div>
    <footer class="footer-band">
      <span>Address: 2748 Tollard Avenue, Suite K West Tollard, NY 14391</span>
      <span>Phone: (716)392-5061</span>
      <span>Fax: (716)392-5087</span>
    </footer>
    <div class="footer-web">www.oswickroot.com</div>
  </main>
</body>
</html>
```